e-commerce store for sport clothing online store "baseball merchandise "web application...

I want to design a UX/UI for my web application website for the online store I will provide you with the following:
1. screen shots of the initial design for the pages>
2. the logo files.
3. The brand guideline file.

the provided files (screen shots) is guideline I want to see CREATIVITY with the UX/UI DESIGN.
PS. PLEASE FOLLOW THE BRANDGUIDE LINE CAREFULLY SPECIALLY THE TYPOGRAPHY & THE COLOR CODES.

PLEASE VISIT THIS WEBSITE brightlane.varomi-qz.com to see more for the screens.

```html
<!DOCTYPE html>
<html lang="en">
<head>
<meta charset="UTF-8">
<title>Checkout – Confirmation</title>
<link rel="stylesheet" href="https://fonts.googleapis.com/css2?family=Titillium+Web:wght@600;700&family=Lato:wght@400;700&display=swap">
<style>
  :root {
    --navy: #10244a;
    --ink: #111111;
    --muted: #3a3a3a;
    --canvas: #e9ecf1;
    --surface: #ffffff;
    --button: #000000;
    --line: #1a1a1a;
    --thumb-trunks: #7cc59a;
    --thumb-cap: #c9ccd1;
  }
  * { margin: 0; padding: 0; box-sizing: border-box; }
  html, body { width: 839px; height: 1200px; overflow: hidden; }
  body { background: var(--canvas); font-family: "Lato", sans-serif; color: var(--ink); }

  .screen {
    position: absolute; left: 147px; top: 0;
    width: 544px; height: 1200px;
    background: var(--surface);
    overflow: hidden;
  }
  .app-bar {
    position: absolute; left: 0; top: 0; width: 100%; height: 122px;
    background: var(--navy);
  }
  .app-bar .back { position: absolute; left: 34px; top: 47px; width: 28px; height: 28px; }
  .app-bar h1 {
    position: absolute; left: 0; right: 0; top: 44px; text-align: center;
    font-family: "Titillium Web", sans-serif; font-weight: 700; font-size: 24px; color: #fff;
  }

  .stepper { position: absolute; left: 0; top: 0; width: 100%; }
  .stepper .track { position: absolute; top: 206px; left: 120px; width: 304px; height: 1.5px; background: var(--line); }
  .step { position: absolute; top: 176px; width: 140px; margin-left: -70px; text-align: center; }
  .step .dot {
    width: 60px; height: 60px; margin: 0 auto; border-radius: 50%;
    background: var(--navy); color: #fff;
    font-family: "Titillium Web", sans-serif; font-weight: 700; font-size: 28px; line-height: 60px;
  }
  .step .label { margin-top: 11px; font-size: 18px; line-height: 24px; color: var(--navy); }

  .section-title { position: absolute; left: 23px; top: 330px; font-size: 22px; font-weight: 700; }

  .item { position: absolute; left: 23px; width: 498px; }
  .item .thumb {
    position: absolute; left: 0; top: 0; width: 98px; height: 98px;
    border-radius: 6px; border: 1px solid #e6e6e6;
  }
  .item .name {
    position: absolute; left: 121px; top: 8px; width: 220px;
    font-family: "Titillium Web", sans-serif; font-weight: 700; font-size: 21px; line-height: 27px;
  }
  .item .unit { font-size: 15px; color: var(--muted); }
  .item .qty { font-size: 18px; color: var(--muted); }
  .item .price {
    position: absolute; right: 0; top: 8px;
    font-family: "Titillium Web", sans-serif; font-weight: 700; font-size: 22px; color: var(--navy);
  }
  .item-trunks { top: 426px; }
  .item-trunks .thumb { background: linear-gradient(160deg, #93d3ac, var(--thumb-trunks)); }
  .item-trunks .unit { position: absolute; left: 121px; top: 64px; }
  .item-trunks .qty { position: absolute; left: 121px; top: 88px; }
  .item-cap { top: 533px; }
  .item-cap .thumb { background: linear-gradient(180deg, #f2f2f2, var(--thumb-cap)); }
  .item-cap .unit { position: absolute; left: 121px; top: 36px; }
  .item-cap .qty { position: absolute; left: 121px; top: 87px; }

  .summary { position: absolute; left: 32px; right: 33px; top: 935px; }
  .summary .row { display: flex; justify-content: space-between; height: 41px; font-size: 18px; }
  .summary .row .amount { font-weight: 700; color: var(--navy); }

  .action-bar {
    position: absolute; left: 0; right: 0; top: 1110px; height: 90px;
    background: var(--surface); border-radius: 14px 14px 0 0;
    box-shadow: 0 -10px 24px rgba(0,0,0,0.12);
  }
  .place-order {
    position: absolute; left: 19px; right: 18px; top: 12px; height: 66px;
    background: var(--button); color: #fff; border: none; border-radius: 6px;
    font-family: "Titillium Web", sans-serif; font-weight: 700; font-size: 21px;
  }
</style>
</head>
<body>
  <main class="screen">
    <header class="app-bar">
      <svg class="back" viewBox="0 0 28 28" aria-label="Back">
        <path d="M25 14H4M13 4L3 14l10 10" fill="none" stroke="#fff" stroke-width="3" stroke-linecap="round" stroke-linejoin="round"/>
      </svg>
      <h1>Checkout</h1>
    </header>

    <nav class="stepper" aria-label="Checkout steps">
      <div class="track"></div>
      <div class="step" style="left:120px"><div class="dot">1</div><div class="label">Shipping<br>Details</div></div>
      <div class="step" style="left:271px"><div class="dot">2</div><div class="label">Payment<br>Details</div></div>
      <div class="step" style="left:424px"><div class="dot">3</div><div class="label">Confirmation</div></div>
    </nav>

    <h2 class="section-title">Items</h2>

    <article class="item item-trunks">
      <div class="thumb" role="img" aria-label="Product photo: kids green patterned swim trunks"></div>
      <div class="name">Splashly Kids Swim Trunks</div>
      <div class="unit">23.000 KD</div>
      <div class="qty">Qty: 1</div>
      <div class="price">23.000 KD</div>
    </article>

    <article class="item item-cap">
      <div class="thumb" role="img" aria-label="Product photo: grey trucker cap with fish patch"></div>
      <div class="name">Bass Trcker Cap</div>
      <div class="unit">13.000 KD</div>
      <div class="qty">Qty: 2</div>
      <div class="price">26.000 KD</div>
    </article>

    <section class="summary">
      <div class="row"><span>Subtotal</span><span class="amount">49.000 KD</span></div>
      <div class="row"><span>Delivery Charge</span><span class="amount">1.000 KD</span></div>
      <div class="row"><span>Total</span><span class="amount">50.000 KD</span></div>
    </section>

    <footer class="action-bar">
      <button class="place-order">Place Order</button>
    </footer>
  </main>
</body>
</html>
```